RWT Fittings Ltd Business Cards

We need a business card with our business logo. We provide window and door installations on high-rises in west coast British Colombia, Canada.

I would like my business information and details on one side of the card, and the other side the company name with logo

Target Market(s)

General Contractors

Industry/Entity Type

Construction

Contact Information for Business Card

one side i want my company name and logo in the dark theme logo that i provided

Requirements
Must have
• Marco Peltieri, 16045518293, RWTFittings@mailbox-demo.com, 1407-5194 Linden Row Burnaby BC, V5H 2K9, Owner & Manager

```html
<!DOCTYPE html>
<html lang="en">
<head>
<meta charset="utf-8">
<title>RWT Fittings Ltd Business Cards</title>
<link rel="stylesheet" href="https://fonts.googleapis.com/css2?family=Roboto:wght@400;500;700&display=swap">
<style>
  :root {
    --bg: #232323;
    --card: #1f1f22;
    --card-edge: #2a2a2e;
    --blue: #27a6e3;
    --grey: #a9a9a9;
    --white: #f2f2f2;
    --photo-dark: #2b2724;
    --photo-light: #5a544e;
  }
  * { margin: 0; padding: 0; box-sizing: border-box; }
  html, body { width: 1200px; height: 780px; overflow: hidden; background: var(--bg); }
  body { font-family: "Roboto", sans-serif; color: var(--white); }
  .canvas {
    width: 1200px; height: 780px;
    display: flex; align-items: center; justify-content: center; gap: 40px;
  }
  .card {
    position: relative; width: 540px; height: 310px; overflow: hidden;
    border-radius: 4px; box-shadow: 0 18px 40px rgba(0,0,0,.55);
  }
  /* front: contact side */
  .card--front { background: var(--card); }
  .brand {
    position: absolute; display: flex; align-items: center; gap: 10px;
    font-weight: 700; color: var(--blue); letter-spacing: .5px;
  }
  .card--front .brand { left: 30px; top: 28px; font-size: 24px; }
  .brand__mark { width: 18px; height: 18px; background: var(--blue); flex: none; }
  .contact {
    position: absolute; left: 30px; top: 96px; font-size: 13px; line-height: 1.45;
    color: var(--white);
  }
  .contact__address { margin-bottom: 10px; }
  .contact__row { display: flex; align-items: center; gap: 8px; }
  .contact__row svg { width: 12px; height: 12px; flex: none; }
  .emblem-area {
    position: absolute; right: 0; bottom: 0; width: 300px; height: 170px;
    background: linear-gradient(135deg, rgba(20,20,22,0) 0%, #141416 45%, #2c2c30 100%);
  }
  .person {
    position: absolute; right: 36px; top: 96px; text-align: right;
  }
  .person__name { font-size: 25px; font-weight: 700; line-height: 1.1; }
  .person__first { color: var(--blue); }
  .person__last { color: var(--grey); }
  .person__role { font-size: 13px; font-weight: 500; margin-top: 4px; color: var(--white); }
  .accent-bar {
    position: absolute; right: 0; top: 96px; width: 16px; height: 48px; background: var(--blue);
  }
  /* back: brand side */
  .card--back {
    background: radial-gradient(ellipse at 70% 40%, var(--photo-light) 0%, var(--photo-dark) 70%);
  }
  .card--back .brand {
    left: 50%; top: 50%; transform: translate(-50%, -50%); font-size: 34px; gap: 14px;
    white-space: nowrap;
  }
  .card--back .brand__mark { width: 26px; height: 26px; }
</style>
</head>
<body>
<main class="canvas">
  <section class="card card--front">
    <div class="brand"><span class="brand__mark"></span>RWT Fittings Ltd</div>
    <div class="contact">
      <p class="contact__address">1407-5194 Linden Row<br>Burnaby BC, V5H 2K9</p>
      <p class="contact__row">
        <svg viewBox="0 0 24 24" aria-hidden="true"><path fill="#27a6e3" d="M6.6 10.8a15 15 0 0 0 6.6 6.6l2.2-2.2c.3-.3.7-.4 1-.2 1.1.4 2.3.6 3.6.6.6 0 1 .4 1 1V20c0 .6-.4 1-1 1A17 17 0 0 1 3 4c0-.6.4-1 1-1h3.5c.6 0 1 .4 1 1 0 1.3.2 2.5.6 3.6.1.3 0 .7-.2 1z"/></svg>
        1604 551 8293
      </p>
      <p class="contact__row">
        <svg viewBox="0 0 24 24" aria-hidden="true"><rect x="2" y="5" width="20" height="14" rx="2" fill="#27a6e3"/><path d="M3 6l9 7 9-7" fill="none" stroke="#1f1f22" stroke-width="2"/></svg>
        RWTFittings@mailbox-demo.com
      </p>
    </div>
    <div class="person">
      <p class="person__name"><span class="person__first">Marco</span> <span class="person__last">Peltieri</span></p>
      <p class="person__role">Owner &amp; Manager</p>
    </div>
    <div class="accent-bar"></div>
    <div class="emblem-area" role="img" aria-label="Large faint embossed brand decoration"></div>
  </section>

  <section class="card card--back" role="img" aria-label="Softly blurred interior room photograph behind the company name">
    <div class="brand"><span class="brand__mark"></span>RWT Fittings Ltd</div>
  </section>
</main>
</body>
</html>
```